Hacienda Monte Verda Business cards

We would like 3 individual business cards with the logo you designed:

1) Marta Pellingford - Phone: 206 555 0147
2) Theodore R Pellingford - Phone 206 555 0183
3) Dana Moreth - Phone 310-555-0162

Address for all three cards:
7218 142nd Ave NE
Larkfield, WA 98077
HaciendaMonteVerda@brindlemail.com

```html
<!DOCTYPE html>
<html lang="en">
<head>
<meta charset="utf-8">
<title>Hacienda Monte Verda – Business Card</title>
<link href="https://fonts.googleapis.com/css2?family=Mulish:wght@400;700&display=swap" rel="stylesheet">
<style>
  :root {
    --page-bg: #e6e6e4;
    --card-light: #ffffff;
    --card-shade: #dedede;
    --ink: #1c1c1c;
    --ink-soft: #3a3a3a;
  }
  html, body {
    margin: 0;
    width: 1200px;
    height: 871px;
    overflow: hidden;
    background: var(--page-bg);
    font-family: "Mulish", "Century Gothic", sans-serif;
  }
  .business-card {
    position: absolute;
    left: 180px;
    top: 195px;
    width: 840px;
    height: 480px;
    background: linear-gradient(135deg, var(--card-light) 0%, #f6f6f6 45%, var(--card-shade) 100%);
    box-shadow: 0 6px 18px rgba(0,0,0,0.18);
    color: var(--ink);
  }
  .contact-block {
    position: absolute;
    left: 112px;
    top: 178px;
  }
  .holder-name {
    margin: 0 0 22px 0;
    font-weight: 700;
    font-size: 24px;
    letter-spacing: 0.2px;
  }
  .contact-list {
    list-style: none;
    margin: 0;
    padding: 0;
    font-size: 15px;
    color: var(--ink-soft);
  }
  .contact-item {
    display: flex;
    align-items: flex-start;
    gap: 18px;
    margin-bottom: 12px;
    line-height: 1.55;
  }
  .contact-icon {
    width: 14px;
    height: 16px;
    flex: none;
    margin-top: 3px;
  }
  .brand-mark {
    position: absolute;
    right: 70px;
    top: 112px;
    display: flex;
    align-items: center;
    gap: 12px;
  }
  .brand-dot {
    width: 12px;
    height: 12px;
    border-radius: 50%;
    background: var(--ink);
  }
  .brand-name {
    font-weight: 400;
    font-size: 24px;
    letter-spacing: 1.2px;
    color: var(--ink);
    white-space: nowrap;
  }
</style>
</head>
<body>
  <div class="business-card">
    <div class="contact-block">
      <h1 class="holder-name">Marta Pellingford</h1>
      <ul class="contact-list">
        <li class="contact-item">
          <svg class="contact-icon" viewBox="0 0 14 16" aria-hidden="true">
            <rect x="3" y="0.8" width="8" height="14.4" rx="1.5" fill="none" stroke="#1c1c1c" stroke-width="1.4"/>
            <line x1="6" y1="12.6" x2="8" y2="12.6" stroke="#1c1c1c" stroke-width="1.4"/>
          </svg>
          <span>206 555 0147</span>
        </li>
        <li class="contact-item">
          <svg class="contact-icon" viewBox="0 0 14 16" aria-hidden="true">
            <path d="M7 15 C3 10 1.5 7.5 1.5 5.5 A5.5 5.5 0 0 1 12.5 5.5 C12.5 7.5 11 10 7 15 Z" fill="none" stroke="#1c1c1c" stroke-width="1.4"/>
            <circle cx="7" cy="5.6" r="1.8" fill="#1c1c1c"/>
          </svg>
          <span>7218 142nd Ave NE<br>Larkfield, WA 98077</span>
        </li>
        <li class="contact-item">
          <svg class="contact-icon" viewBox="0 0 14 16" aria-hidden="true">
            <rect x="0.8" y="3.5" width="12.4" height="9" fill="none" stroke="#1c1c1c" stroke-width="1.4"/>
            <polyline points="0.8,3.8 7,8.8 13.2,3.8" fill="none" stroke="#1c1c1c" stroke-width="1.4"/>
          </svg>
          <span>HaciendaMonteVerda@brindlemail.com</span>
        </li>
      </ul>
    </div>
    <div class="brand-mark">
      <span class="brand-dot"></span>
      <span class="brand-name">Hacienda Monte Verda</span>
    </div>
  </div>
</body>
</html>
```